Modern Business Card For A Digital Advertising Company

I'll be print on the Pell Prints Velour paper http://us.pellprints.com/products/velour/business-cards.html
Need's to be modern and use the color palette of the logo or gray scales. I think integrating the pixelation of the logo in to the card and having it wrap from one side to the other could be interesting. My company provides ad operations, web development, and number of other services to websites around the world. You can see my website at http://www.zantorhq.com
Contact info on the card needs to have
Owen Lasko
President
p.318.204.6637
owen@zantorhq.com
http://www.zantorhq.com
Doesn't necessarily need to be in that order
Website owners
Business

```html
<!DOCTYPE html>
<html lang="en">
<head>
<meta charset="utf-8">
<title>Zantor – Business Card</title>
<link rel="stylesheet" href="https://fonts.googleapis.com/css2?family=Arimo:wght@700&family=Open+Sans:ital,wght@0,600;0,700;1,600&display=swap">
<style>
  :root {
    --backdrop: #d9d9d9;
    --card-black: #050505;
    --steel-dark: #3a3a3a;
    --steel-mid: #7d7d7d;
    --steel-light: #d6d6d6;
    --paper-white: #f7f7f7;
    --brand-green: #7cc242;
    --text-white: #ffffff;
    --text-dark: #2a2a2a;
  }
  html, body {
    margin: 0;
    width: 1200px;
    height: 911px;
    overflow: hidden;
    background: var(--backdrop);
  }
  .business-card {
    position: absolute;
    left: 78px;
    top: 136px;
    width: 1016px;
    height: 582px;
    box-shadow: 0 6px 14px rgba(0,0,0,0.35);
  }
  .business-card svg { display: block; }
  .role-label { font: italic 600 27px "Open Sans", sans-serif; fill: var(--text-dark); }
  .person-name { font: 700 58px "Arimo", sans-serif; fill: var(--text-white); letter-spacing: -1px; }
  .contact-phone { font: 700 39px "Open Sans", sans-serif; fill: var(--text-white); }
  .contact-line { font: 600 25px "Open Sans", sans-serif; fill: var(--text-white); }
  .icon-glyph { font: 700 26px "Open Sans", sans-serif; fill: var(--text-white); }
  .brand-name { font: 700 64px "Open Sans", sans-serif; fill: var(--brand-green); letter-spacing: 3px; }
</style>
</head>
<body>
<div class="business-card">
  <svg width="1016" height="582" viewBox="0 0 1016 582" xmlns="http://www.w3.org/2000/svg">
    <defs>
      <linearGradient id="card-base" x1="0" y1="0" x2="1" y2="0.3">
        <stop offset="0" stop-color="#8a8a8a"/>
        <stop offset="0.45" stop-color="#2a2a2a"/>
        <stop offset="1" stop-color="var(--card-black)"/>
      </linearGradient>
      <linearGradient id="swoosh-top" x1="0" y1="0" x2="1" y2="1">
        <stop offset="0" stop-color="#6a6a6a"/>
        <stop offset="0.5" stop-color="#d8d8d8"/>
        <stop offset="1" stop-color="#3c3c3c"/>
      </linearGradient>
      <linearGradient id="swoosh-bottom" x1="0" y1="0" x2="1" y2="0">
        <stop offset="0" stop-color="#ffffff"/>
        <stop offset="0.6" stop-color="#9a9a9a"/>
        <stop offset="1" stop-color="#2e2e2e"/>
      </linearGradient>
      <linearGradient id="name-panel" x1="0" y1="0" x2="0" y2="1">
        <stop offset="0" stop-color="#4a4a4a"/>
        <stop offset="0.5" stop-color="#151515"/>
        <stop offset="1" stop-color="#5a5a5a"/>
      </linearGradient>
      <linearGradient id="row-bar" x1="0" y1="0" x2="1" y2="0">
        <stop offset="0" stop-color="#ffffff"/>
        <stop offset="1" stop-color="#9a9a9a"/>
      </linearGradient>
      <linearGradient id="tab" x1="0" y1="0" x2="1" y2="0">
        <stop offset="0" stop-color="#9c9c9c"/>
        <stop offset="1" stop-color="#e6e6e6"/>
      </linearGradient>
      <linearGradient id="brand-frame" x1="0" y1="0" x2="1" y2="1">
        <stop offset="0" stop-color="#ffffff"/>
        <stop offset="0.6" stop-color="#c4c4c4"/>
        <stop offset="1" stop-color="#777777"/>
      </linearGradient>
      <linearGradient id="brand-inner" x1="0" y1="0" x2="1" y2="1">
        <stop offset="0" stop-color="var(--paper-white)"/>
        <stop offset="1" stop-color="#bdbdbd"/>
      </linearGradient>
    </defs>

    <rect class="card-base" width="1016" height="582" fill="url(#card-base)"/>
    <path class="accent-swoosh-top" d="M0 0 H110 C220 30 320 110 330 180 L0 180 Z" fill="url(#swoosh-top)" opacity="0.85"/>
    <path class="accent-swoosh-top-dark" d="M110 0 H1016 V40 C700 20 420 40 330 180 C320 110 220 30 110 0 Z" fill="var(--card-black)"/>
    <path class="accent-swoosh-bottom" d="M150 512 C300 520 500 530 650 525 L1016 560 V582 H215 C190 560 170 535 150 512 Z" fill="url(#swoosh-bottom)"/>

    <path class="name-panel" d="M114 168 H530 L557 205 V498 H114 Z" fill="url(#name-panel)"/>
    <path class="role-tab" d="M3 203 H168 L160 246 H3 Z" fill="url(#tab)"/>
    <text class="role-label" x="18" y="236">President</text>
    <text class="person-name" x="171" y="243">Owen Lasko</text>

    <g class="contact-rows">
      <path d="M114 312 H220 L214 362 H114 Z" fill="url(#row-bar)"/>
      <path d="M114 370 H220 L214 420 H114 Z" fill="url(#row-bar)"/>
      <path d="M114 429 H220 L214 479 H114 Z" fill="url(#row-bar)"/>

      <g class="icon icon-phone">
        <circle cx="185" cy="337" r="23" fill="#444" stroke="#ddd" stroke-width="3"/>
        <rect x="177" y="324" width="16" height="26" rx="3" fill="none" stroke="#fff" stroke-width="2.5"/>
        <circle cx="185" cy="345" r="1.6" fill="#fff"/>
      </g>
      <g class="icon icon-email">
        <circle cx="185" cy="395" r="23" fill="#444" stroke="#ddd" stroke-width="3"/>
        <text class="icon-glyph" x="185" y="404" text-anchor="middle">@</text>
      </g>
      <g class="icon icon-web">
        <circle cx="185" cy="454" r="23" fill="#444" stroke="#ddd" stroke-width="3"/>
        <text class="icon-glyph" x="185" y="464" text-anchor="middle">i</text>
      </g>

      <text class="contact-phone" x="227" y="359">318.204.6637</text>
      <text class="contact-line" x="227" y="408">owen@zantorhq.com</text>
      <text class="contact-line" x="230" y="469">www.zantorhq.com</text>
    </g>

    <g class="brand-block">
      <path d="M667 110 H960 Q1000 110 1000 150 V515 L960 550 H667 Z" fill="url(#brand-frame)"/>
      <path d="M683 126 H950 Q984 126 984 160 V505 L952 534 H683 Z" fill="url(#brand-inner)"/>
      <rect class="brand-square" x="810" y="260" width="34" height="34" fill="var(--brand-green)"/>
      <text class="brand-name" x="827" y="390" text-anchor="middle">ZANTOR</text>
    </g>
  </svg>
</div>
</body>
</html>
```